U.S. Popcorn company needs business cards

We are a popcorn company that manufactures popcorn and sells it to grocery stores worldwide. Our theme is "Americana" and our logo is U.S. route 66 which is the most famous highway in the U.S.

We would like the design to be simple and to use both sides. On the back side we would like to see just the logo and website. The front would be normal details

Target Market(s)

Wholesalers, grocers and distributors

Industry/Entity Type

Manufacture

Contact Information for Business Card

Business name: Prairie Lantern Popcorn
Phone: +1 555 308 4726
Email: Dale@prairielanternpopcorn.com
website: www.prairielanternpopcorn.com
Tag Line: "Worth every kernel"
Name: Dale Whitcombe
Title: Founder/President

Requirements
Must have
• Either this design should be fun or clean and simple. I will let you show me your thougths.
Nice to have
• Anything that ties in the real Hwy Route 66.
• Colors might need to be red, white and blue incorporated.
Should not have
• Not be too busy.

```html
<!DOCTYPE html>
<html lang="en">
<head>
<meta charset="utf-8">
<title>Prairie Lantern Popcorn – Business Cards</title>
<link rel="stylesheet" href="https://fonts.googleapis.com/css2?family=Open+Sans:ital,wght@0,400;0,600;0,700;1,400&display=swap">
<style>
  :root {
    --navy: #1d2f6f;
    --red: #d42a2a;
    --card: #f7f7f7;
    --backdrop: #e4e4e4;
    --ink: #1d2f6f;
  }
  * { margin: 0; padding: 0; box-sizing: border-box; }
  html, body { width: 1200px; height: 576px; overflow: hidden; }
  body {
    background: var(--backdrop);
    font-family: "Open Sans", Arial, sans-serif;
    position: relative;
  }
  .card {
    position: absolute;
    top: 138px;
    width: 484px;
    height: 294px;
    background: var(--card);
    border-radius: 6px;
    overflow: hidden;
  }
  .card--back { left: 80px; }
  .card--front { left: 602px; }

  .brand-name {
    position: absolute;
    color: var(--navy);
    font-weight: 700;
    text-align: center;
    line-height: 1.1;
    text-transform: uppercase;
  }
  .card--back .brand-name {
    left: 0; right: 0; top: 103px;
    font-size: 30px;
  }
  .card--front .brand-name {
    left: 310px; width: 150px; top: 68px;
    font-size: 18px;
  }

  .back-website {
    position: absolute;
    left: 0; right: 0; top: 256px;
    display: flex; align-items: center; justify-content: center;
    gap: 12px;
    font-size: 11px; font-weight: 700;
    color: var(--navy);
  }
  .back-website .rule {
    width: 48px; height: 2px; background: var(--navy); border-radius: 1px;
  }
  .back-website .domain { color: var(--red); }

  .edge-tab {
    position: absolute; left: 0; top: 26px;
    width: 13px; height: 50px;
    background: var(--navy);
    border-radius: 0 25px 25px 0;
  }
  .person { position: absolute; left: 26px; top: 32px; }
  .person__name { color: var(--red); font-size: 17px; font-weight: 600; line-height: 1.1; }
  .person__title { color: var(--ink); font-size: 12px; font-style: italic; margin-top: 2px; }

  .contact {
    position: absolute; left: 28px; top: 212px;
    list-style: none;
    color: var(--ink); font-size: 13px;
  }
  .contact li { display: flex; align-items: center; gap: 12px; height: 18px; }
  .contact svg { width: 11px; height: 11px; fill: var(--red); flex: none; }

  .tagline {
    position: absolute; right: 30px; top: 246px;
    color: var(--ink); font-size: 14px;
  }
</style>
</head>
<body>
  <section class="card card--back" aria-label="Card back">
    <div class="brand-name">Prairie Lantern<br>Popcorn</div>
    <div class="back-website">
      <span class="rule"></span>
      <span>www.<span class="domain">prairielanternpopcorn</span>.com</span>
      <span class="rule"></span>
    </div>
  </section>

  <section class="card card--front" aria-label="Card front">
    <span class="edge-tab"></span>
    <div class="person">
      <div class="person__name">Dale Whitcombe</div>
      <div class="person__title">Founder/President</div>
    </div>
    <div class="brand-name">Prairie Lantern<br>Popcorn</div>
    <ul class="contact">
      <li>
        <svg viewBox="0 0 12 12" aria-hidden="true"><path d="M1 4c0-2 2-3 5-3s5 1 5 3v1H8.5V3.5h-5V5H1zM3 6h6l2 5H1z"/></svg>
        +1 555 308 4726
      </li>
      <li>
        <svg viewBox="0 0 12 12" aria-hidden="true"><path d="M0 2h12v8H0z M0 2l6 5 6-5" stroke="#f7f7f7" stroke-width="1"/></svg>
        Dale@prairielanternpopcorn.com
      </li>
      <li>
        <svg viewBox="0 0 12 12" aria-hidden="true"><circle cx="6" cy="6" r="5.5"/><path d="M0.5 6h11M6 0.5v11M2 3h8M2 9h8" stroke="#f7f7f7" stroke-width="0.8" fill="none"/></svg>
        www.prairielanternpopcorn.com
      </li>
    </ul>
    <p class="tagline">"Worth every kernel"</p>
  </section>
</body>
</html>
```